Business card design for my company.
I would like the card's background colour to be black. You can also see our web site to get an idea of our brand. https://www.tmwhomecrafting.com.au/
- Name
- Email

```html
<!DOCTYPE html>
<html lang="en">
<head>
<meta charset="utf-8">
<title>TMW Home Crafting – Business Card</title>
<link rel="stylesheet" href="https://fonts.googleapis.com/css2?family=Montserrat:wght@400;500;700&display=swap">
<style>
  :root {
    --stage: #2b2b2b;
    --card-black: #141414;
    --brand-green: #1c9a48;
    --green-light: #27b35a;
    --green-dark: #137a37;
    --text-white: #ffffff;
    --text-soft: #e6e6e6;
  }
  * { box-sizing: border-box; margin: 0; padding: 0; }
  html, body {
    width: 1200px; height: 689px; overflow: hidden;
    background: var(--stage);
    font-family: "Montserrat", Arial, sans-serif;
  }
  .canvas {
    position: relative; width: 1200px; height: 689px;
    display: flex; align-items: center; justify-content: center; gap: 40px;
  }
  .card {
    position: relative; width: 540px; height: 309px;
    border-radius: 22px; overflow: hidden;
    box-shadow: 0 18px 40px rgba(0,0,0,.45);
  }
  .card-back {
    background: linear-gradient(120deg, var(--green-light) 0%, var(--brand-green) 50%, var(--green-dark) 100%);
  }
  .card-front { background: var(--card-black); }

  .holder {
    position: absolute; top: 34px; right: 26px;
    display: flex; align-items: stretch; gap: 14px;
  }
  .holder-text { text-align: right; }
  .holder-name {
    color: var(--brand-green); font-weight: 700; font-size: 30px; line-height: 1.05;
  }
  .holder-title {
    color: var(--text-white); font-weight: 500; font-size: 15px; margin-top: 4px;
  }
  .holder-bar { width: 9px; background: var(--brand-green); }

  .brand {
    position: absolute; left: 34px; top: 108px;
    display: flex; align-items: center; gap: 12px;
  }
  .brand-square { width: 22px; height: 22px; background: var(--brand-green); }
  .brand-name {
    color: var(--text-white); font-weight: 700; font-size: 24px; letter-spacing: 1.5px;
  }

  .contacts {
    position: absolute; left: 34px; bottom: 28px;
    list-style: none; display: flex; flex-direction: column; gap: 7px;
  }
  .contacts .gap-after { margin-bottom: 12px; }
  .contact {
    display: flex; align-items: center; gap: 10px;
    color: var(--text-soft); font-size: 14px; font-weight: 400;
  }
  .contact svg { width: 14px; height: 14px; flex: none; fill: var(--brand-green); }
</style>
</head>
<body>
<main class="canvas">
  <section class="card card-back" role="img" aria-label="Repeating company name pattern in tones of green"></section>

  <section class="card card-front">
    <div class="holder">
      <div class="holder-text">
        <p class="holder-name">Ryan Holloway</p>
        <p class="holder-title">General Manager</p>
      </div>
      <span class="holder-bar"></span>
    </div>

    <div class="brand">
      <span class="brand-square"></span>
      <span class="brand-name">TMW HOME CRAFTING</span>
    </div>

    <ul class="contacts">
      <li class="contact gap-after">
        <svg viewBox="0 0 24 24"><path d="M12 2a7 7 0 0 0-7 7c0 5 7 13 7 13s7-8 7-13a7 7 0 0 0-7-7zm0 9.5A2.5 2.5 0 1 1 12 6.5a2.5 2.5 0 0 1 0 5z"/></svg>
        Northport, Tasmania, Australia
      </li>
      <li class="contact">
        <svg viewBox="0 0 24 24"><path d="M6.6 10.8a15 15 0 0 0 6.6 6.6l2.2-2.2c.3-.3.7-.4 1-.2 1.1.4 2.3.6 3.6.6.6 0 1 .4 1 1V20c0 .6-.4 1-1 1A17 17 0 0 1 3 4c0-.6.4-1 1-1h3.5c.6 0 1 .4 1 1 0 1.3.2 2.5.6 3.6.1.3 0 .7-.2 1z"/></svg>
        0400 123 456
      </li>
      <li class="contact">
        <svg viewBox="0 0 24 24"><path d="M3 5h18v14H3zm2 2v.5l7 4.5 7-4.5V7zm0 2.8V17h14V9.8l-7 4.5z"/></svg>
        info@tmwhomecrafting.com.au
      </li>
      <li class="contact">
        <svg viewBox="0 0 24 24"><path d="M12 2a10 10 0 1 0 0 20 10 10 0 0 0 0-20zm6.9 9h-3a15 15 0 0 0-1.3-5.5A8 8 0 0 1 18.9 11zM12 4c.9 1.2 1.8 3.6 1.9 7h-3.8c.1-3.4 1-5.8 1.9-7zM9.4 5.5A15 15 0 0 0 8.1 11h-3a8 8 0 0 1 4.3-5.5zM5.1 13h3a15 15 0 0 0 1.3 5.5A8 8 0 0 1 5.1 13zm6.9 7c-.9-1.2-1.8-3.6-1.9-7h3.8c-.1 3.4-1 5.8-1.9 7zm2.6-1.5a15 15 0 0 0 1.3-5.5h3a8 8 0 0 1-4.3 5.5z"/></svg>
        www.tmwhomecrafting.com.au
      </li>
    </ul>
  </section>
</main>
</body>
</html>
```